Web Design job - Condo Debts Collection Business needs a Web Design

I need a site for a client, who works with condo debts collection, and ensure all revenues provided by condo fees will be always available to the building manager of condo on a specific date, regardless of defaults.
I have the visual identity (logo, slogan and colors) of the company, and some requirements on layout (kind of slider, menu options, phone number on a noble position, etc) - maybe I can do a sketch, but I like the idea of give some freedom to designer.

*** PLEASE, we have no interest in templates. We want something new***

Target Market(s)

I have two targets for this design: - Condominium's building manager. This target is looking for a solution to overdue debts on it's condo. - Residents on condominiums. This target wants to live in a better place, where their neighbors pay their condominium fees on time.

Number of Pages Required

1 page

Requirements
Must have
• - Slider with title, some short text related, a nice image (I prefer happy and/or peaceful family, people doing business, happy friends, and so on).
• - I have a special attention to menu. I'm looking for one I can have a nice effect, more elegant, charming, kind of innovative.
• - Phone number on the top (or clearly visible).
• - Member log in area or icon on the top (or clearly visible).
• - News/articles area.
• - Modern fonts, with good quality, sans-serif on areas where reading is more intensive (prefer Google web-fonts).
• - Colors specified on attached files.
Nice to have
• - Clear background color, cause it's better to read larger texts (like articles). Dark backgrounds makes reading difficult.
• - A site with effects (like shadows, lines, curves, gradients, lights) is usually pretty.
• - I pay attention on beautiful footers.
Should not have
• - Images with a lot of money (I don't sell richness, I sell tranquility, peace, harmony, safety).
• - Poor menu.

```html
<!DOCTYPE html>
<html lang="en">
<head>
<meta charset="utf-8">
<title>Calvora – Cobrança Condominial</title>
<link href="https://fonts.googleapis.com/css2?family=Poppins:wght@400;500;600;700&display=swap" rel="stylesheet">
<style>
:root{
  --gold:#c8a13a;
  --gold-light:#e2b94d;
  --ink:#2b2b2b;
  --text:#7a7a7a;
  --cream:#fdf5e3;
  --dark:#2a2727;
  --darker:#211e1e;
  --white:#ffffff;
}
*{box-sizing:border-box;margin:0;padding:0}
html,body{width:1200px;height:3197px;overflow:hidden}
body{font-family:'Poppins',sans-serif;color:var(--ink);background:var(--white);position:relative}
.abs{position:absolute}
p{font-size:13.5px;line-height:24px;color:var(--text)}

/* header */
.site-header{position:absolute;top:0;left:0;width:1200px;height:96px;background:var(--white)}
.brand{position:absolute;left:85px;top:18px;display:flex;align-items:center;gap:14px}
.brand-square{width:52px;height:52px;background:var(--gold)}
.brand-name{font-size:42px;font-weight:700;line-height:40px;color:var(--ink)}
.brand-tag{font-size:9px;letter-spacing:1px;color:var(--ink);font-weight:500;margin-top:2px}
.topbar{position:absolute;left:410px;top:0;width:790px;height:44px;border-bottom:1px solid #e5e5e5}
.phone{position:absolute;left:425px;top:10px;display:flex;align-items:center;gap:12px;font-size:15px;font-weight:500}
.member{position:absolute;left:595px;top:11px;font-size:14px;color:var(--gold);font-weight:500}
.main-nav{position:absolute;left:510px;top:58px;display:flex;align-items:center;font-size:16px;font-weight:500}
.main-nav a{color:var(--ink);text-decoration:none}
.main-nav .sep{margin:0 26px;color:var(--ink)}

/* hero */
.hero{position:absolute;top:96px;left:0;width:1200px;height:472px;
  background:linear-gradient(180deg,#6f9cc6 0%,#b9cde0 35%,#d8d4c6 55%,#5f6a3a 70%,#4a5a2c 100%)}
.hero-name{position:absolute;left:568px;top:210px;font-size:44px;font-weight:700;color:var(--white);text-shadow:0 2px 8px rgba(0,0,0,.35)}

/* welcome */
.welcome{position:absolute;top:568px;left:0;width:1200px;height:347px;background:var(--cream);box-shadow:0 28px 40px -20px rgba(0,0,0,.18)}
.section-title{font-size:32px;font-weight:600;text-align:center;color:var(--ink)}
.divider{display:block;margin:8px auto 0}
.welcome p{width:1010px;margin:14px auto 0;text-align:center}
.btn{display:block;margin:0 auto;background:var(--gold);color:var(--white);font-size:14px;font-weight:500;border-radius:20px;text-align:center;text-decoration:none}

/* feature rows */
.feature-title{font-size:22px;font-weight:600;line-height:31px;color:var(--ink)}
.rule{width:64px;height:2px;background:var(--gold);margin:10px 0 16px}
.ticks{list-style:none}
.ticks li{font-size:13.5px;color:var(--ink);display:flex;align-items:center;gap:10px;height:41px}

/* experience band */
.experience{position:absolute;top:1820px;left:0;width:1200px;height:307px;
  background:linear-gradient(180deg,#3b4350 0%,#2c3039 60%,#23262d 100%)}
.experience h2{font-size:28px;font-weight:600;color:var(--white);text-align:center;margin-top:52px}
.experience p{color:#e8e8e8;text-align:center;width:920px;margin:0 auto}

/* news */
.news-card .meta{font-size:13px;color:var(--ink);display:flex;gap:22px;align-items:center}
.news-card h3{font-size:15.5px;font-weight:600;line-height:23px;margin-top:14px}
.news-card p{font-size:12.5px;line-height:21px;margin-top:8px}
.news-card .line{width:64px;height:1px;background:var(--ink);margin:14px 0 8px}
.news-card .more{font-size:12.5px;color:var(--gold)}
.thumb{background:linear-gradient(160deg,#eef1f4,#c9d3dc 60%,#9fb0c0)}
.thumb.warm{background:linear-gradient(160deg,#6d5a48,#a58c6f 55%,#3c3a3a)}

/* footer */
.site-footer{position:absolute;top:2945px;left:0;width:1200px;height:205px;background:var(--dark)}
.site-footer p{color:#cfcfcf;font-size:12.5px;line-height:22px}
.footer-title{font-size:17px;font-weight:600;color:var(--white)}
.contact-line{font-size:12.5px;color:#d8d8d8;display:flex;gap:8px;align-items:flex-start;line-height:21px;margin-bottom:8px}
.social{display:flex;gap:12px}
.social span{width:10px;height:10px;border-radius:50%;background:var(--gold);display:block}
.copyright{position:absolute;top:3150px;left:0;width:1200px;height:47px;background:var(--darker);color:#a8a8a8;font-size:12px;text-align:center;line-height:47px}
</style>
</head>
<body>

<header class="site-header">
  <div class="brand">
    <div class="brand-square"></div>
    <div>
      <div class="brand-name">calvora</div>
      <div class="brand-tag">COBRANÇA CONDOMINIAL</div>
    </div>
  </div>
  <div class="topbar">
    <div class="phone">
      <svg width="22" height="22" viewBox="0 0 22 22"><rect x="3" y="3" width="16" height="16" transform="rotate(45 11 11)" fill="none" stroke="#c8a13a" stroke-width="1.5"/><path d="M8 7.5c.5 3 3 5.8 6.3 6.7l1-1.2-1.6-1-1 .8c-1-.5-2-1.5-2.5-2.5l.8-1-1-1.6z" fill="#c8a13a"/></svg>
      (85) 3000.4418
    </div>
    <div class="member">Member login »</div>
  </div>
  <nav class="main-nav">
    <a href="#">Home</a><span class="sep">|</span>
    <a href="#">About us</a><span class="sep">|</span>
    <a href="#">Services</a><span class="sep">|</span>
    <a href="#">News/articles</a><span class="sep">|</span>
    <a href="#">Contact us</a>
  </nav>
</header>

<section class="hero" role="img" aria-label="Happy family with a child on the father's shoulders in a field at sunset">
  <div class="hero-name">Marcos Alvim Duarte</div>
</section>

<section class="welcome">
  <h2 class="section-title" style="padding-top:56px">Welcome to Calvora</h2>
  <svg class="divider" width="150" height="12" viewBox="0 0 150 12"><line x1="0" y1="9" x2="150" y2="9" stroke="#c8a13a" stroke-width="1"/><polygon points="69,9 75,1 81,9" fill="#c8a13a"/></svg>
  <p>Sed ut perspiciatis unde omnis iste natus error sit voluptatem accusantium doloremque laudantium, totam rem aperiam, eaque ipsa quae ab illo inventore veritatis et quasi architecto beatae vitae dicta sunt explicabo. Nemo enim ipsam voluptatem quia voluptas sit aspernatur aut odit aut fugit, sed quia consequuntur magni dolores eos qui ratione voluptatem sequi nesciunt. Neque porro quisquam est, qui dolorem ipsum quia dolor sit amet, consectetur, adipisci velit, sed quia non numquam eius modi tempora incidunt</p>
  <a class="btn" href="#" style="width:120px;height:38px;line-height:38px;margin-top:26px">Read More</a>
</section>

<section class="abs" style="top:998px;left:85px;width:490px">
  <h2 class="feature-title">Resolving Past Due Condo Association &amp; Homeowner Association (HOA) Dues and Fees</h2>
  <div class="rule"></div>
  <p>Sed ut perspiciatis unde omnis iste natus error sit voluptatem accusantium doloremque laudantium, totam rem aperiam, eaque ipsa quae ab illo inventore veritatis et quasi architecto beatae vitae dicta sunt explicabo. Nemo enim ipsam voluptatem quia voluptas sit aspernatur aut odit aut fugit, sed quia consequuntur magni dolores eos qui ratione voluptatem sequi nesciunt.</p>
  <p style="margin-top:24px">Neque porro quisquam est, qui dolorem ipsum quia dolor sit amet, consectetur, adipisci velit, sed quia non numquam eius modi tempora incidunt</p>
</section>
<div class="abs" role="img" aria-label="Two-storey suburban house with garden and blossoming tree" style="top:1001px;left:613px;width:500px;height:337px;background:linear-gradient(180deg,#3f74c8 0%,#8fb2e0 35%,#b9a895 55%,#5f8f3a 80%,#4c7a2d 100%)"></div>

<div class="abs" role="img" aria-label="Row of townhouses fading into white" style="top:1400px;left:0;width:610px;height:360px;background:linear-gradient(90deg,#8a8079 0%,#b3aba3 40%,#d8d4cf 70%,#ffffff 100%)"></div>
<section class="abs" style="top:1414px;left:613px;width:500px">
  <h2 class="feature-title">Consolidate Condo Association Arrearages through a Chapter 13 Reorganization Plan</h2>
  <p style="color:var(--ink);margin-top:14px;line-height:24px">But I must explain to you how all this mistaken idea of denouncing pleas ure and praising pain was born and I will give</p>
  <ul class="ticks" style="margin-top:4px">
    <li><svg width="12" height="10" viewBox="0 0 12 10"><path d="M1 5l3.5 3.5L11 1.5" fill="none" stroke="#c8a13a" stroke-width="2"/></svg>Sed ut perspiciatis unde omnis iste natus error sit voluptatem</li>
    <li><svg width="12" height="10" viewBox="0 0 12 10"><path d="M1 5l3.5 3.5L11 1.5" fill="none" stroke="#c8a13a" stroke-width="2"/></svg>accusantium doloremque laudantium, totam rem aperiam,</li>
    <li><svg width="12" height="10" viewBox="0 0 12 10"><path d="M1 5l3.5 3.5L11 1.5" fill="none" stroke="#c8a13a" stroke-width="2"/></svg>eaque ipsa quae ab illo inventore veritatis et quasi architecto beatae</li>
    <li><svg width="12" height="10" viewBox="0 0 12 10"><path d="M1 5l3.5 3.5L11 1.5" fill="none" stroke="#c8a13a" stroke-width="2"/></svg>vitae dicta sunt explicabo</li>
    <li><svg width="12" height="10" viewBox="0 0 12 10"><path d="M1 5l3.5 3.5L11 1.5" fill="none" stroke="#c8a13a" stroke-width="2"/></svg>eaque ipsa quae ab illo inventore veritatis et quasi architecto beatae</li>
  </ul>
</section>

<section class="experience" role="img" aria-label="Dark mountain landscape with a climber helping another up a ridge">
  <h2>Trust Our Debt Resolution Experience</h2>
  <div style="width:80px;height:2px;background:var(--gold);margin:8px auto 14px"></div>
  <p>Sed ut perspiciatis unde omnis iste natus error sit voluptatem accusantium doloremque laudantium, totam rem aperiam, eaque ipsa quae ab illo inventore veritatis et quasi architecto beatae vitae dicta sunt explicabo. Nemo enim ipsam voluptatem quia voluptas sit aspernatur aut odit aut fugit, sed quia consequuntur magni dolores eos qui ratione voluptatem sequi nesciunt.</p>
  <p style="margin-top:24px">Neque porro quisquam est, qui dolorem ipsum quia dolor sit amet, consectetur, adipisci velit, sed quia non numquam eius modi tempora incidunt</p>
</section>

<section class="abs" style="top:2180px;left:0;width:1200px">
  <h2 class="section-title">News/articles</h2>
  <div style="width:70px;height:2px;background:var(--gold);margin:6px auto 0"></div>
</section>

<div class="abs thumb" role="img" aria-label="Smiling business team around a laptop" style="top:2255px;left:85px;width:238px;height:258px"></div>
<article class="abs news-card" style="top:2255px;left:350px;width:220px">
  <div class="meta"><span>Posted 05 july 2018</span><span>💬 20</span></div>
  <h3>Sed ut perspiciatis unde omn is iste natus error sit volu</h3>
  <p>Sed ut perspiciatis unde omnis iste natus error sit voluptatem accus antium doloremque laudantium, totam rem aperiam, eaque ipsa quae ab illo inventore veritatis et quasi architecto beatae</p>
  <div class="line"></div><div class="more">Read More</div>
</article>
<div class="abs thumb warm" role="img" aria-label="People meeting at a table with laptop and documents" style="top:2255px;left:613px;width:238px;height:258px"></div>
<article class="abs news-card" style="top:2255px;left:877px;width:230px">
  <div class="meta"><span>Posted 05 july 2018</span><span>💬 20</span></div>
  <h3>Sed ut perspiciatis unde omn is iste natus error sit volu</h3>
  <p>Sed ut perspiciatis unde omnis iste natus error sit voluptatem accus antium doloremque laudantium, totam rem aperiam, eaque ipsa quae ab illo inventore veritatis et quasi architecto beatae</p>
  <div class="line"></div><div class="more">Read More</div>
</article>

<article class="abs news-card" style="top:2540px;left:85px;width:230px">
  <div class="meta"><span>Posted 05 july 2018</span></div>
  <h3>Sed ut perspiciatis unde omn is iste natus error sit volu</h3>
  <p>Sed ut perspiciatis unde omnis iste natus error sit voluptatem accus antium doloremque laudantium, totam rem aperiam, eaque ipsa quae ab illo inventore veritatis et quasi architecto beatae</p>
  <div class="line"></div><div class="more">Read More</div>
</article>
<div class="abs thumb" role="img" aria-label="Smiling business team around a laptop" style="top:2540px;left:350px;width:238px;height:258px"></div>
<article class="abs news-card" style="top:2540px;left:613px;width:230px">
  <div class="meta"><span>Posted 05 july 2018</span></div>
  <h3>Sed ut perspiciatis unde omn is iste natus error sit volu</h3>
  <p>Sed ut perspiciatis unde omnis iste natus error sit voluptatem accus antium doloremque laudantium, totam rem aperiam, eaque ipsa quae ab illo inventore veritatis et quasi architecto beatae</p>
  <div class="line"></div><div class="more">Read More</div>
</article>
<div class="abs thumb" role="img" aria-label="Smiling business team around a laptop" style="top:2540px;left:877px;width:236px;height:258px"></div>

<a class="btn abs" href="#" style="top:2846px;left:540px;width:120px;height:38px;line-height:38px">View All</a>

<footer class="site-footer">
  <div class="abs" style="left:85px;top:22px;display:flex;align-items:center;gap:12px">
    <div style="width:48px;height:48px;background:var(--gold)"></div>
    <div>
      <div style="font-size:38px;font-weight:700;line-height:36px;color:var(--white)">calvora</div>
      <div style="font-size:8.5px;letter-spacing:1px;color:var(--white)">COBRANÇA CONDOMINIAL</div>
    </div>
  </div>
  <p class="abs" style="left:85px;top:93px;width:680px">Sed ut perspiciatis unde omnis iste natus error sit voluptatem accusantium doloremque laudantium, totam rem aperiam, eaque ipsa quae ab illo inventore veritatis et quasi architecto beatae vitae dicta sunt explicabo. Nemo enim ipsam voluptatem quia voluptas sit</p>
  <div class="social abs" style="left:85px;top:178px"><span></span><span></span><span></span><span></span></div>
  <div class="abs" style="left:867px;top:25px;width:290px">
    <div class="footer-title">Contact Us</div>
    <div style="width:34px;height:2px;background:var(--gold);margin:6px 0 12px"></div>
    <div class="contact-line"><svg width="12" height="14" viewBox="0 0 12 14"><path d="M2 1l3 1 .5 3-1.5 1c.8 1.8 2 3 3.5 3.8l1.2-1.4 3 .8-.5 3C6 12 1 7 2 1z" fill="#fff"/></svg>(85) 3000.4418</div>
    <div class="contact-line"><svg width="13" height="14" viewBox="0 0 13 14"><rect x="1" y="3" width="11" height="8" fill="#fff"/><path d="M1 3l5.5 4.5L12 3" fill="none" stroke="#2a2727"/></svg>contato@calvora.com.br</div>
    <div class="contact-line"><svg width="10" height="14" viewBox="0 0 10 14"><path d="M5 1a4 4 0 0 1 4 4c0 3-4 8-4 8S1 8 1 5a4 4 0 0 1 4-4z" fill="#fff"/><circle cx="5" cy="5" r="1.5" fill="#2a2727"/></svg><span>Av. Praia Serena, 820<br>Sala 402, Ed. Horizonte,<br>CEP: 60.000-000, Centro, Fortaleza-CE</span></div>
  </div>
</footer>
<div class="copyright">Copyright © 2018. All Rights Reserved</div>

</body>
</html>
```